Clear Harbor Business card

We are a company that owns 2 compliance software programs for TV, Radio and Cable industries as well as an online job board. We need a professional business card that incorproates all three logos.

```html
<!DOCTYPE html>
<html lang="en">
<head>
<meta charset="utf-8">
<title>Clear Harbor Business Card</title>
<link href="https://fonts.googleapis.com/css2?family=Roboto:wght@400;500;700&display=swap" rel="stylesheet">
<style>
  :root {
    --navy: #1e1b6b;
    --red: #e3321f;
    --blue: #2e7fc4;
    --ink: #22223a;
    --paper: #fbfbfa;
    --backdrop: #e6e6e8;
    --rule: #b9b9bd;
  }
  * { box-sizing: border-box; margin: 0; padding: 0; }
  html, body { width: 1200px; height: 874px; overflow: hidden; }
  body {
    background: var(--backdrop);
    font-family: "Roboto", Arial, sans-serif;
    color: var(--ink);
    position: relative;
  }
  .card {
    position: absolute;
    left: 280px;
    width: 640px;
    height: 366px;
    background: var(--paper);
    box-shadow: 0 6px 18px rgba(0,0,0,0.18);
    overflow: hidden;
  }
  .card--front { top: 51px; }
  .card--back { top: 457px; }

  .brand-row {
    position: absolute;
    display: flex;
    align-items: center;
  }
  .brand {
    display: flex;
    align-items: center;
    gap: 6px;
    font-weight: 700;
    color: var(--navy);
  }
  .brand__name {
    white-space: nowrap;
    line-height: 1.1;
  }
  .brand__mark {
    width: 9px; height: 9px;
    background: var(--red);
    flex: none;
  }
  .brand--jobs { color: var(--blue); }
  .brand--jobs .brand__mark { background: var(--blue); border-radius: 50%; }
  .brand-divider {
    width: 1.5px;
    background: var(--navy);
    flex: none;
  }

  .card--front .brand-row {
    left: 0; right: 0; top: 118px;
    justify-content: center;
    gap: 18px;
  }
  .card--front .brand { font-size: 19px; }
  .card--front .brand-divider { height: 62px; }

  .web-band {
    position: absolute;
    left: 0; right: 0; top: 226px;
    height: 60px;
    background: var(--navy);
    display: flex;
    align-items: center;
    justify-content: center;
    color: #fff;
    font-size: 15px;
    letter-spacing: 7px;
  }

  .card--back .brand-row {
    left: 28px; top: 122px;
    gap: 10px;
  }
  .card--back .brand { font-size: 12.5px; gap: 5px; }
  .card--back .brand__mark { width: 7px; height: 7px; }
  .card--back .brand-divider { height: 44px; }

  .split-rule {
    position: absolute;
    left: 396px; top: 30px;
    width: 2px; height: 300px;
    background: linear-gradient(to bottom, transparent, var(--rule) 20%, var(--rule) 80%, transparent);
  }

  .holder {
    position: absolute;
    left: 424px; top: 50px;
  }
  .holder__name {
    font-size: 24px;
    font-weight: 700;
    color: var(--navy);
    letter-spacing: 0.5px;
    line-height: 1;
  }
  .holder__title {
    font-size: 15px;
    font-weight: 500;
    color: var(--red);
    margin-top: 4px;
    text-transform: uppercase;
  }
  .holder__address {
    margin-top: 16px;
    font-size: 14px;
    line-height: 1.35;
  }
  .contact-list {
    list-style: none;
    margin-top: 12px;
    font-size: 14px;
    line-height: 1.35;
  }
  .contact-list li {
    display: flex;
    align-items: center;
    gap: 8px;
  }
  .contact-list svg { width: 12px; height: 12px; flex: none; fill: var(--navy); }
</style>
</head>
<body>

<section class="card card--front" aria-label="Card front">
  <div class="brand-row">
    <div class="brand"><span class="brand__mark"></span><span class="brand__name">Clear Harbor<br>Broadcast</span></div>
    <div class="brand-divider"></div>
    <div class="brand"><span class="brand__mark"></span><span class="brand__name">Clear Harbor<br>Cable</span></div>
    <div class="brand-divider"></div>
    <div class="brand brand--jobs"><span class="brand__mark"></span><span class="brand__name">StageRoster<br>.com</span></div>
  </div>
  <div class="web-band">www.clearharbor.example</div>
</section>

<section class="card card--back" aria-label="Card back">
  <div class="brand-row">
    <div class="brand"><span class="brand__mark"></span><span class="brand__name">Clear Harbor<br>Broadcast</span></div>
    <div class="brand-divider"></div>
    <div class="brand"><span class="brand__mark"></span><span class="brand__name">Clear Harbor<br>Cable</span></div>
    <div class="brand-divider"></div>
    <div class="brand brand--jobs"><span class="brand__mark"></span><span class="brand__name">StageRoster<br>.com</span></div>
  </div>

  <div class="split-rule"></div>

  <div class="holder">
    <h1 class="holder__name">DANA PRYOR</h1>
    <p class="holder__title">CEO/Founder</p>
    <p class="holder__address">214 Wharf Row<br>Kettle Bay, Maine 04100</p>
    <ul class="contact-list">
      <li><svg viewBox="0 0 12 12"><path d="M2.5 1l2 2.3-1 1.2c.6 1.4 1.6 2.4 3 3l1.2-1 2.3 2-1.2 1.8C5 10 2 7 1 1.8z"/></svg>555 210 4471</li>
      <li><svg viewBox="0 0 12 12"><path d="M3 0h6v12H3zM4 1.5v8h4v-8z"/></svg>555 382 9056</li>
      <li><svg viewBox="0 0 12 12"><path d="M3 0h6v3H3zM0 4h12v6h-2V8H2v2H0zM3 9h6v3H3z"/></svg>555 647 1139</li>
      <li><svg viewBox="0 0 12 12"><path d="M0 2h12v8H0zM1 3l5 3.5L11 3v-.2H1z"/></svg>dana@clearharbor.example</li>
      <li><svg viewBox="0 0 12 12"><circle cx="6" cy="6" r="6"/></svg>www.clearharbor.example</li>
    </ul>
  </div>
</section>

</body>
</html>
```